Venture Capital Investment Firm

We are looking to overhaul our existing website (substantially), with only using the same logos (which we can provide).
We are an investment firm that focuses on making loans to late stage technology companies. Our site should ultimately look like other venture capital firms, and look modern and fresh. We have an existing website www.norvellhub.com which this will be replacing, although we will be using a lot of the existing written content, and potentially the numbers of pages we will need, we are not wed to anything else. Please feel free to shoot any questions at any time and thank you in advance for your help!
Websites we like as examples:
https://www.tesmarkfund.com/
https://www.brindlewoodpartners.com/
Target Market(s)
Potential investors who will invest in our firm, as well as potentially companies that are looking to borrow money from us.
Coding
Coded - Design and coding required
Number of Pages Required
5+ page
Colors
Designer to choose colors to be used in the design.
Look and feel

```html
<!DOCTYPE html>
<html lang="en">
<head>
<meta charset="utf-8">
<title>Norvell Hub – Investment Partners</title>
<link rel="stylesheet" href="https://fonts.googleapis.com/css2?family=Cinzel:wght@600;700&family=Montserrat:wght@400;500;600;700&display=swap">
<style>
:root{
  --navy:#0c0a45;
  --navy-deep:#08073a;
  --ink:#1b1b2e;
  --grey:#8a8a96;
  --line:#e4e4ea;
  --soft:#f6f6f9;
  --white:#ffffff;
}
*{box-sizing:border-box;margin:0;padding:0}
html,body{width:1200px;height:3877px;overflow:hidden}
body{position:relative;background:var(--white);font-family:"Montserrat",sans-serif;color:var(--ink)}
.abs{position:absolute}
.serif{font-family:"Cinzel",serif}
.btn{position:absolute;display:flex;align-items:center;justify-content:center;gap:8px;background:var(--navy);color:var(--white);font-weight:700;border-radius:30px;letter-spacing:.3px}
.btn .arr{width:14px;height:14px;border-radius:50%;background:var(--white);position:relative}
.btn .arr::after{content:"";position:absolute;left:4px;top:4px;width:4px;height:4px;border-top:2px solid var(--navy);border-right:2px solid var(--navy);transform:rotate(45deg)}

/* header */
.site-header{position:absolute;left:0;top:0;width:1200px;height:95px;background:var(--white);border-top:4px solid var(--navy)}
.brand{position:absolute;left:143px;top:14px;display:flex;align-items:center;gap:14px}
.brand-dot{width:52px;height:52px;border-radius:50%;background:var(--navy)}
.brand-name{font-family:"Cinzel",serif;font-weight:700;font-size:34px;color:var(--navy);line-height:1}
.brand-sub{font-size:10px;font-weight:600;color:var(--navy);letter-spacing:.6px;margin-top:4px}
.nav{position:absolute;left:490px;top:32px;display:flex;gap:30px;font-size:13.5px;font-weight:500;color:var(--ink)}
.nav .active{border-bottom:2px solid var(--navy);padding-bottom:8px}

/* hero */
.hero{position:absolute;left:0;top:95px;width:1200px;height:680px;background:linear-gradient(180deg,#1d4d8a 0%,#3a78b4 35%,#8a7e86 62%,#d98a45 80%,#5a3b2a 100%)}
.hero-title{position:absolute;left:144px;top:232px;font-family:"Cinzel",serif;font-weight:700;font-size:92px;color:var(--white);line-height:1}
.hero-sub{position:absolute;left:146px;top:346px;font-size:18px;font-weight:600;color:var(--white)}
.dots{position:absolute;left:547px;top:667px;display:flex;gap:7px}
.dots span{width:17px;height:17px;border-radius:50%;background:var(--white)}
.dots .on{background:var(--navy);box-shadow:inset 0 0 0 4px var(--white)}

/* welcome */
.welcome-art{position:absolute;left:166px;top:820px;width:346px;height:400px}
.welcome-title{position:absolute;left:577px;top:872px;font-family:"Cinzel",serif;font-weight:700;font-size:40px;color:var(--navy)}
.welcome-copy{position:absolute;left:577px;top:936px;width:460px;font-size:12px;line-height:24.8px;color:#6b6b78}

/* partners */
.partners{position:absolute;left:0;top:1212px;width:1200px;height:600px;background:linear-gradient(160deg,#12305a 0%,#1e4a75 40%,#0f2748 100%)}
.partners-title{position:absolute;left:0;top:1382px;width:1200px;text-align:center;font-family:"Cinzel",serif;font-weight:700;font-size:40px;color:var(--white)}
.partners-copy{position:absolute;left:210px;top:1455px;width:780px;text-align:center;font-size:12px;line-height:25px;color:var(--white)}
.diamond{position:absolute;width:242px;height:242px;border-radius:18px;transform:rotate(45deg);border:5px solid var(--white);box-shadow:0 8px 20px rgba(0,0,0,.25)}
.d-one{left:200px;top:1644px;background:linear-gradient(135deg,#1b1a64,#0d0c46)}
.d-two{left:479px;top:1644px;background:linear-gradient(135deg,#8d8e98,#54555f)}
.d-three{left:757px;top:1644px;background:linear-gradient(135deg,#24226e,#0f0d48)}
.pillar{position:absolute;width:260px;text-align:center;color:var(--white)}
.pillar svg{display:block;margin:0 auto 8px}
.pillar h3{font-size:19px;font-weight:700;margin-bottom:6px}
.pillar p{font-size:12px;line-height:19px}
.pillar .more{display:inline-block;margin-top:10px;padding:7px 16px;background:var(--white);border-radius:16px;font-size:11px;font-weight:700;color:var(--navy)}
.d-two-text .more{color:#6a6a74}

/* team */
.section-title{position:absolute;left:0;width:1200px;text-align:center;font-family:"Cinzel",serif;font-weight:700;font-size:40px;color:var(--navy)}
.member{position:absolute;width:300px;text-align:center}
.ring{position:relative;width:240px;height:240px;margin:0 auto;border-radius:50%;border:1px solid var(--line);background:var(--white);box-shadow:0 2px 10px rgba(0,0,0,.04)}
.portrait{position:absolute;left:25px;top:25px;width:190px;height:190px;border-radius:50%;background:radial-gradient(circle at 50% 40%,#8a8a8a,#1f1f1f 75%)}
.badge{position:absolute;left:93px;top:203px;width:54px;height:54px;border-radius:50%;background:var(--navy);border:3px solid var(--white)}
.member h4{margin-top:36px;font-size:16px;font-weight:600;color:var(--ink)}
.member .role{margin-top:8px;font-size:11px;color:#9a9aa4;letter-spacing:.4px}
.member .bio{margin-top:10px;font-size:11.5px;line-height:20px;color:#7a7a86}
.member .btn{position:relative;margin:14px auto 0;width:128px;height:40px;font-size:14px}

/* news */
.news{position:absolute;left:0;top:2600px;width:1200px;height:900px;background:var(--soft)}
.card{position:absolute;background:var(--white);border:1px solid var(--line)}
.photo{position:absolute}
.card .date{position:absolute;font-size:12px;font-weight:600;color:var(--ink)}
.card h5{position:absolute;font-size:18px;font-weight:500;line-height:24px;color:var(--ink)}
.card .txt{position:absolute;font-size:11.5px;line-height:25px;color:#8a8a96}
.card .link{position:absolute;font-size:15px;font-weight:700;color:var(--navy);letter-spacing:.3px}

/* footer */
.footer-contact{position:absolute;width:230px;text-align:center;color:var(--white)}
.footer-contact .ic{width:72px;height:72px;margin:0 auto;border:2px solid var(--white);border-radius:50%;display:flex;align-items:center;justify-content:center}
.footer-contact h6{margin-top:20px;font-size:15px;font-weight:700;letter-spacing:.3px}
.footer-contact p{margin-top:10px;font-size:12px;line-height:18px}
.social{position:absolute;left:143px;top:3826px;display:flex;gap:7px}
.social span{width:30px;height:30px;border:1.5px solid var(--white);border-radius:50%}
.legal{position:absolute;left:669px;top:3834px;font-size:11.5px;color:var(--white)}
</style>
</head>
<body>

<header class="site-header">
  <div class="brand">
    <div class="brand-dot"></div>
    <div>
      <div class="brand-name">Norvell Hub</div>
      <div class="brand-sub">INVESTMENT PARTNERS, LLC</div>
    </div>
  </div>
  <nav class="nav">
    <span class="active">HOME</span><span>STRATEGY</span><span>ABOUT US</span><span>TEAM</span><span>NEWS</span><span>CONTACT</span><span>INVESTORS</span>
  </nav>
</header>

<section class="hero" role="img" aria-label="Suspension bridge and city skyline at dusk"></section>
<svg class="abs" style="left:0;top:560px" width="1200" height="250" viewBox="0 0 1200 250">
  <path d="M0 20 Q600 400 1200 20 L1200 250 L0 250 Z" fill="#ffffff"/>
  <path d="M70 60 Q600 370 1130 60" fill="none" stroke="#0c0a45" stroke-width="7"/>
  <circle cx="600" cy="205" r="30" fill="#ffffff" stroke="#0c0a45" stroke-width="5"/>
</svg>
<h1 class="hero-title">Norvell Hub</h1>
<p class="hero-sub">At vero eos et accusamus et iusto odio dignissimos ducimus</p>
<div class="btn" style="left:146px;top:415px;width:186px;height:53px;font-size:16px">GET STARTED <span class="arr"></span></div>
<div class="dots"><span></span><span></span><span class="on"></span><span></span><span></span></div>

<section>
  <div class="welcome-art" role="img" aria-label="Financial charts and analyst at work inside a large circle">
    <svg width="346" height="400" viewBox="0 0 346 400">
      <defs><linearGradient id="wg" x1="0" y1="0" x2="1" y2="1"><stop offset="0" stop-color="#5d7f8f"/><stop offset="1" stop-color="#c9d2d8"/></linearGradient></defs>
      <circle cx="173" cy="175" r="172" fill="url(#wg)"/>
      <circle cx="173" cy="175" r="118" fill="#ffffff"/>
    </svg>
  </div>
  <h2 class="welcome-title">Welcome to NorvellHub</h2>
  <p class="welcome-copy">Norvell Hub is a private investment firm unique in its dual focus on life science and technology credit opportunities. Our ambidextrous approach to investing reflects a broad recognition and appreciation for the critical role intellectual property plays in the successful commercialization of products. We apply our extensive industry expertise to assess the revenue visibility created by these assets and offer a range of creative financing solutions.</p>
  <div class="btn" style="left:576px;top:1114px;width:162px;height:47px;font-size:14px">READ MORE <span class="arr"></span></div>
</section>

<section class="partners" role="img" aria-label="Blurred trading screen with rising green line chart"></section>
<svg class="abs" style="left:0;top:1200px" width="1200" height="620" viewBox="0 0 1200 620">
  <path d="M0 0 L1200 0 L1200 10 Q600 180 0 10 Z" fill="#ffffff"/>
  <path d="M0 607 Q600 450 1200 607 L1200 620 L0 620 Z" fill="#ffffff"/>
  <polyline points="380,560 520,420 640,340 720,380 840,260 940,300 1200,120" fill="none" stroke="#2fd3c2" stroke-width="2.5" opacity=".7"/>
</svg>
<svg class="abs" style="left:0;top:1805px" width="1200" height="160" viewBox="0 0 1200 160"><rect width="1200" height="160" fill="#ffffff"/></svg>
<h2 class="partners-title">Partners for Growth</h2>
<p class="partners-copy">Our focus spans the life science and technology industries, two sectors where intellectual property (IP) is an integral driver of asset and enterprise value. Our broad experience in investing, technology evaluation, and product forecasting affords us a unique understanding of the value of assets in these dynamic sectors, allowing us to see value where others cannot.</p>

<div class="diamond d-one"></div>
<div class="diamond d-two"></div>
<div class="diamond d-three"></div>

<div class="pillar" style="left:191px;top:1650px">
  <svg width="56" height="64" viewBox="0 0 56 64" fill="none" stroke="#fff" stroke-width="2.5"><path d="M6 28 L28 6 L50 28"/><path d="M12 24 V58 H44 V24"/><path d="M20 48 L36 32"/><circle cx="21" cy="35" r="3"/><circle cx="35" cy="46" r="3"/></svg>
  <h3>LIFE SCIENCES</h3>
  <p>Lorem ipsum dolor sit amet,<br>consectetur adipiscing elit, sed<br>do eiusmod tempor</p>
  <span class="more">READ MORE ›</span>
</div>
<div class="pillar d-two-text" style="left:470px;top:1650px">
  <svg width="64" height="64" viewBox="0 0 64 64" fill="none" stroke="#fff" stroke-width="2.5"><circle cx="38" cy="26" r="10"/><circle cx="38" cy="26" r="17" stroke-dasharray="6 4"/><path d="M22 40 Q12 34 14 22 Q18 8 32 8"/><path d="M20 44 H32 M21 50 H31"/></svg>
  <h3>TECHNOLOGY</h3>
  <p>Lorem ipsum dolor sit amet,<br>consectetur adipiscing elit, sed<br>do eiusmod tempor</p>
  <span class="more">READ MORE ›</span>
</div>
<div class="pillar" style="left:748px;top:1650px">
  <svg width="76" height="64" viewBox="0 0 76 64" fill="none" stroke="#fff" stroke-width="2.5"><rect x="4" y="6" width="26" height="52" rx="4"/><rect x="46" y="6" width="26" height="52" rx="4"/><circle cx="38" cy="32" r="11"/><path d="M38 25 V39 M34 29 Q38 25 42 29 M34 35 Q38 39 42 35"/></svg>
  <h3>TRANSACTION TYPES</h3>
  <p>Lorem ipsum dolor sit amet,<br>consectetur adipiscing elit, sed<br>do eiusmod tempor</p>
  <span class="more">READ MORE ›</span>
</div>

<h2 class="section-title" style="top:2037px">Our Team</h2>

<div class="member" style="left:115px;top:2131px">
  <div class="ring"><div class="portrait" role="img" aria-label="Portrait of Marek Holloway"></div><div class="badge"></div></div>
  <h4>MAREK HOLLOWAY</h4><div class="role">MANAGING PARTNER</div>
  <p class="bio">Risus commodo viverra maecenas<br>accumsan lacus vel facilisis.</p>
  <div class="btn">EMAIL ME <span class="arr"></span></div>
</div>
<div class="member" style="left:450px;top:2131px">
  <div class="ring"><div class="portrait" role="img" aria-label="Portrait of Dorian Castellane"></div><div class="badge"></div></div>
  <h4>DORIAN CASTELLANE</h4><div class="role">MANAGING PARTNER</div>
  <p class="bio">Risus commodo viverra maecenas<br>accumsan lacus vel facilisis.</p>
  <div class="btn">EMAIL ME <span class="arr"></span></div>
</div>
<div class="member" style="left:784px;top:2131px">
  <div class="ring"><div class="portrait" role="img" aria-label="Portrait of Tobin Ashcroft"></div><div class="badge"></div></div>
  <h4>TOBIN ASHCROFT</h4><div class="role">PARTNER</div>
  <p class="bio">Risus commodo viverra maecenas<br>accumsan lacus vel facilisis.</p>
  <div class="btn">EMAIL ME <span class="arr"></span></div>
</div>

<section class="news"></section>
<svg class="abs" style="left:0;top:2595px" width="1200" height="110" viewBox="0 0 1200 110"><path d="M0 0 L1200 0 Q600 210 0 0 Z" fill="#ffffff"/></svg>
<h2 class="section-title" style="top:2783px">Latest News</h2>

<article class="card" style="left:140px;top:2880px;width:297px;height:506px">
  <div class="photo" role="img" aria-label="Business meeting over printed financial charts" style="left:2px;top:2px;width:292px;height:220px;background:linear-gradient(135deg,#3a3d44,#b9bcc2)"></div>
  <div class="date" style="left:22px;top:254px">Nov 19,2019</div>
  <h5 style="left:22px;top:284px;width:250px">Sed ut perspiciatis unde omnis iste natus</h5>
  <p class="txt" style="left:22px;top:348px;width:255px">Ut enim ad minima venia quis nostreierci tationem ullam corporis suscipitoriosan isi ut aliquid ex ea commodi ependeritq ui in ea voluptate velit .</p>
  <div class="link" style="left:22px;top:464px">READ MORE</div>
</article>

<article class="card" style="left:453px;top:2876px;width:606px;height:249px">
  <div class="photo" role="img" aria-label="Handshake in front of city towers" style="left:3px;top:3px;width:234px;height:241px;background:linear-gradient(135deg,#5c86b6,#c5d2e0)"></div>
  <div class="date" style="left:272px;top:30px">Nov 19,2019</div>
  <h5 style="left:272px;top:59px;width:300px">Sed ut perspiciatis unde omnis iste natus error</h5>
  <p class="txt" style="left:272px;top:114px;width:300px">Ut enim ad minima veniam, quis nostreierci tationem ullam corporis suscipit laboriosan isi ut aliquid ex ea eprehenderitq utate velit .</p>
  <div class="link" style="left:272px;top:208px">READ MORE</div>
</article>

<article class="card" style="left:453px;top:3140px;width:606px;height:246px">
  <div class="photo" role="img" aria-label="Hands on a tablet with glowing data charts" style="left:3px;top:3px;width:236px;height:240px;background:linear-gradient(135deg,#c8cdd4,#7a8088)"></div>
  <div class="date" style="left:272px;top:30px">Nov 19,2019</div>
  <h5 style="left:272px;top:59px;width:300px">Sed ut perspiciatis unde omnis iste natus error</h5>
  <p class="txt" style="left:272px;top:114px;width:300px">Ut enim ad minima veniam, quis nostreierci tationem ullam corporis suscipit laboriosan isi ut aliquid ex ea eprehenderitq utate velit .</p>
  <div class="link" style="left:272px;top:208px">READ MORE</div>
</article>

<svg class="abs" style="left:0;top:3455px" width="1200" height="422" viewBox="0 0 1200 422">
  <path d="M0 250 Q600 -110 1200 250 L1200 422 L0 422 Z" fill="#0c0a45"/>
  <path d="M70 200 Q600 -90 1130 200" fill="none" stroke="#0c0a45" stroke-width="5"/>
  <circle cx="600" cy="36" r="30" fill="#ffffff" stroke="#0c0a45" stroke-width="5"/>
</svg>

<div class="footer-contact" style="left:112px;top:3589px">
  <div class="ic"><svg width="28" height="20" viewBox="0 0 28 20"><rect width="28" height="20" rx="2" fill="#fff"/><path d="M1 2 L14 11 L27 2" fill="none" stroke="#0c0a45" stroke-width="2"/></svg></div>
  <h6>MEDIA INQUIRIES</h6><p>media@norvellhub.com</p>
</div>
<div class="footer-contact" style="left:368px;top:3589px">
  <div class="ic"><svg width="28" height="20" viewBox="0 0 28 20"><rect width="28" height="20" rx="2" fill="#fff"/><path d="M1 2 L14 11 L27 2" fill="none" stroke="#0c0a45" stroke-width="2"/></svg></div>
  <h6>GENERAL INQUIRIES</h6><p>inquiries@norvellhub.com</p>
</div>
<div class="footer-contact" style="left:632px;top:3589px">
  <div class="ic"><svg width="22" height="30" viewBox="0 0 22 30"><path d="M11 29 C4 19 1 15 1 10 A10 10 0 0 1 21 10 C21 15 18 19 11 29 Z" fill="none" stroke="#fff" stroke-width="2.5"/><circle cx="11" cy="10" r="3.5" fill="#fff"/></svg></div>
  <h6>MAIN OFFICE</h6><p>240 Alder Lane #310<br>Larkspur Bay, CA 94177</p>
</div>
<div class="footer-contact" style="left:867px;top:3589px">
  <div class="ic"><svg width="28" height="20" viewBox="0 0 28 20"><rect width="28" height="20" rx="2" fill="#fff"/><path d="M1 2 L14 11 L27 2" fill="none" stroke="#0c0a45" stroke-width="2"/></svg></div>
  <h6>CAREERS</h6><p>career@norvellhub.com</p>
</div>

<div class="social"><span></span><span></span><span></span><span></span></div>
<p class="legal">Copyrights @ 2019 NORVELL HUB All Rights Reserved &nbsp;|&nbsp; Privacy Policy</p>

</body>
</html>
```